New business card for a regional office of a US M&A company

We need business card for a finance company, office based in Hong Kong , our Head office is in US, our business is to Merge and acquires companies , the new office will be a regional office for the Asia Pacific region. We want to use the head office logo as attached ( but don't have to be exactly the same, can be a variation to it) as a base and then add Asia Pacific alongside the logo.
We would prefer to have be bilingual Eng + Chinese, although we don't really have Chinese company name .

Industry/Entity Type

Business

Contact Information for Business Card

Clara Jo Tsang
 

VP,
APAC M&A Operations
Orin Vantage Asia Pacific Limited
 
Unit 1407, K18
18 Tai Lok Shan Road, 
Hong Kong 
 
M: +852 6038 1742
T : +852 2836 4100
F : +852 2836 4177
VOIP: 4158
 
cjtsang@orinvantage.com

Font styles to use
Serif
Sans Serif

Colors

Designer to choose colors to be used in the design.

Requirements
Must have
• APAC Office

```html
<!DOCTYPE html>
<html lang="en">
<head>
<meta charset="utf-8">
<title>Orin Vantage – APAC Business Card</title>
<link href="https://fonts.googleapis.com/css2?family=Open+Sans:wght@400;600;700;800&display=swap" rel="stylesheet">
<style>
  :root {
    --bg: #e6e6e6;
    --card: #ffffff;
    --navy: #0d2a46;
    --teal: #21b0cc;
    --teal-deep: #1ea5c0;
    --grey-text: #505559;
  }
  * { margin: 0; padding: 0; box-sizing: border-box; }
  html, body { width: 1200px; height: 1000px; overflow: hidden; }
  body {
    background: var(--bg);
    font-family: "Open Sans", Arial, sans-serif;
    position: relative;
  }
  .card {
    position: absolute;
    left: 239px;
    width: 698px;
    height: 397px;
    border-radius: 14px;
    overflow: hidden;
  }
  .card-front { top: 82px; background: var(--card); }
  .card-back { top: 520px; background: var(--teal); }

  .holder-name {
    position: absolute; left: 54px; top: 72px;
    font-size: 25px; font-weight: 600; color: var(--navy); letter-spacing: 0.3px;
  }
  .holder-title {
    position: absolute; left: 54px; top: 108px;
    font-size: 17px; font-weight: 600; color: var(--grey-text);
  }
  .contact-list {
    position: absolute; left: 54px; top: 175px; list-style: none;
  }
  .contact-list li {
    display: flex; align-items: center; height: 19.5px;
    font-size: 15px; color: var(--grey-text); letter-spacing: 1px;
  }
  .contact-list svg { width: 12px; height: 12px; margin-right: 11px; flex: none; }
  .office-address {
    position: absolute; left: 55px; top: 276px;
    font-size: 17px; line-height: 22px; color: var(--grey-text);
  }
  .brand-mark {
    position: absolute; left: 480px; top: 98px;
    width: 80px; height: 80px; background: var(--navy);
  }
  .brand-name {
    position: absolute; right: 38px; top: 276px;
    font-size: 40px; font-weight: 800; color: var(--teal); letter-spacing: 1px;
  }
  .footer-band { position: absolute; left: 0; bottom: 0; width: 698px; height: 32px; }
  .voip {
    position: absolute; left: 469px; bottom: 5px;
    font-size: 16px; font-weight: 600; color: #fff; letter-spacing: 0.5px;
  }

  .back-pattern {
    position: absolute; inset: 0;
    background: linear-gradient(180deg, #22b2cd 0%, #1faac5 100%);
  }
  .back-mark {
    position: absolute; left: 314px; top: 110px;
    width: 70px; height: 70px; background: #fff;
  }
  .back-name {
    position: absolute; left: 0; right: 0; top: 222px; text-align: center;
    font-size: 50px; font-weight: 800; color: #fff; letter-spacing: 1px;
  }
</style>
</head>
<body>

<section class="card card-front">
  <h1 class="holder-name">CLARA JO TSANG</h1>
  <p class="holder-title">VP, APAC M&amp;A Operations</p>

  <ul class="contact-list">
    <li>
      <svg viewBox="0 0 12 12" aria-hidden="true"><rect x="3" y="0.5" width="6" height="11" rx="1" fill="none" stroke="#21b0cc" stroke-width="1.3"/><rect x="5" y="9.3" width="2" height="1" fill="#21b0cc"/></svg>
      +852 6038 1742
    </li>
    <li>
      <svg viewBox="0 0 12 12" aria-hidden="true"><path d="M2.5 1 L4.5 1 L5.3 3.6 L4 4.6 C4.7 6.1 5.9 7.3 7.4 8 L8.4 6.7 L11 7.5 L11 9.5 C11 10.3 10.3 11 9.5 11 C5 10.6 1.4 7 1 2.5 C1 1.7 1.7 1 2.5 1 Z" fill="#21b0cc"/></svg>
      +852 2836 4100
    </li>
    <li>
      <svg viewBox="0 0 12 12" aria-hidden="true"><rect x="3" y="0.5" width="6" height="3" fill="#21b0cc"/><rect x="0.5" y="4" width="11" height="5" rx="1" fill="#21b0cc"/><rect x="3" y="7.5" width="6" height="4" fill="#fff" stroke="#21b0cc" stroke-width="1"/></svg>
      +852 2836 4177
    </li>
    <li>
      <svg viewBox="0 0 12 12" aria-hidden="true"><rect x="0.5" y="2" width="11" height="8" rx="0.8" fill="#21b0cc"/><path d="M1 2.6 L6 6.4 L11 2.6" fill="none" stroke="#fff" stroke-width="1"/></svg>
      cjtsang@orinvantage.com
    </li>
  </ul>

  <p class="office-address">Unit 1407, K18 18 Tai Lok<br>Shan Road, Hong Kong</p>

  <div class="brand-mark" aria-hidden="true"></div>
  <p class="brand-name">ORIN VANTAGE</p>

  <svg class="footer-band" viewBox="0 0 698 32" preserveAspectRatio="none" aria-hidden="true">
    <path d="M0 13 L398 13 C410 13 412 17 404 19 L0 19 Z" fill="#0d2a46"/>
    <path d="M0 21 L395 21 C425 21 440 6 470 4 L698 4 L698 32 L0 32 Z" fill="#21b0cc"/>
  </svg>
  <p class="voip">VOIP: 4158</p>
</section>

<section class="card card-back">
  <div class="back-pattern" role="img" aria-label="Repeating brand pattern in tonal teal"></div>
  <div class="back-mark" aria-hidden="true"></div>
  <p class="back-name">ORIN VANTAGE</p>
</section>

</body>
</html>
```